Blood Testing Health App

We are looking for a graphics designer to create a web app for us so that we may insert it into a health management website system.
For branding purposes we are at www.Vantiqor.com and we are revamping our website... Example of new colors attached.
How we work...
We are a blood testing company based in the USA.
We offer a blood testing service nationwide in the USA.
We allow customers to order tests directly from us, visit a lab, have their blood drawn, or submit a urine sample, the lab tests it and they send the results back to our computer system and we share it with the customer.
The benefits of this are the customer does not need to go to the doctor and pay for the doctors visit to order these tests, which save them money. The tests are cheaper than going through the doctor. The customer simply uses us to get the test and the results and they can then take the results to their doctor... this process has saved them money. Others may be interested in regular check ups for blood work etc... and this allows them to do it with out needing a doctor, or if you have no insurance, this is a cheaper option too. We are quicker than a doctor, customers do not need appointments etc.
Hopefully you now have a better understanding as to what we do.
Here is the spec.
The app screen size is 750 px wide by 700 px high. ( A pdf is attached to show where the app is going to go, it is on page 3 of the pdf) The customer will have the ability to scroll… therefore the length of the page can be longer.
The app will consist of the following sections
Entry Page –
This will be the first page the user sees upon opening the app. This will be where they are directed from to the sections of the app discussed below. This needs to be branded for VantiQor with a modern look.
1 – Order Test (Giving them the ability to purchase a blood test within the app)
2 – VantiQor Dashboard (A dashboard that has everything they could need to use our service_
How it works Section on entry page – this will be a simple set of graphics showing how the service works. We already have the graphics for this, they do not need to be built again. They are attached to this brief
Basic structure of sections –
Order Test –
This page contains all tests, filed in categories – and Sub categories – Each test needs a link to an Information section – Price – Buy Now – Cart Process
VantiQor Dashboard –
A page of icons along the top of the app
- My Confirmation
- My Nearest Lab
- My Receipt
- My Orders
- My Account
- My Results
- My Inbox
- Contact Us
Sections in more detail -
Order A Test –
Show all categories/ sub categories – There are 23 categories, 14 sub categories, and within these categories are 300 tests - Here is the information for the categories etc - http://www.vantiqor.com/panels.aspx?PanelGroupID=4 Just in case it helps :)
We need to present this in a graphic format that is spacious, modern (brimlake, kivvo web appearance is the direction we are going for) We need it to be clear and not overwhelming to the customer.
Functionality idea…
Customer clicks category/ subcategory and tests appear.
Customer sees small 35 word description. For more information the test opens into a lightbox or expand the container which ever graphic designer believes to be most visually appealing
Buy Now must always be visible, along with price of the test
Buying process explained – Customer clicks buy now –
They are then taken to a Review Order screen ( This contains Order summary and choose payment method – insert payment details )
– Confirm payment –
Confirmation screen appears, thanking them.
They are then taken to the VantiQor Dashboard...
VantiQor Dashboard –
"My Confirmation" - Print Confirmation Order (PDF is in brief, we want this web based not a pdf download)
"My Nearest Lab Location" - This does not need to be designed because the web developer has this part under control, but we do need the icon in the dashboard
"My Receipt" - Print receipt - This does not exist in our system yet. So we need to create this from scratch - It will need to have - The test they are purchasing and the amount of the test - The customers name - The order ID - Must provide printer friendly option too
"My Orders" - This will have a list of orders - At the end of each order will be a status update of either "Test results" "Open order"
A graphic table format would be perfect. This will be linked to relevant results if they have been received. I have also attached a version of what the customer currently sees on our website. We know it is nasty ;) We are redesigning... but the information is there for this section to help design it with the right info. If the results are ready it will say in this list.
"Results Ready" will be a link to show those results once the customer has clicked the link, and the results will appear in the app, under the icons. There must be a printer friendly version too.
"My Results" Developer will sort this page out but we need the icon... It will be exactly like my orders but only show test results
"My Account" - This will be a place for them to update their personal information - Name, DOB, Address, Email Address
"My Inbox" - An inbox interface - Our way of contacting the customer for promotions we are running etc – We need a design of how this screen will appear. We also need the icon in the dashboard to have a notification on it if there are messages in the customers inbox. A little red 1, or circle with number of messages in the inbox.
"Customer Service" - This does not need to be designed because the web developer has this part under control, but we do need the icon in the dashboard
Icons appear along the top of app ( example - Mac icons/ iphone app icons) When the customer clicks an icon the content always appears below the icons
Here is more information for the icons and what should appear when each icon is clicked.
Screens to be designed –
Entry Page
Order A Test Page
Review Order Screen/Payment Screen - Show a lightbox that shows payment has been confirmed. Customer clicks close and are on the Confirmation Screen
VantiQor Dashboard - Screens mentioned in detail above
We can't wait to see your designs!
Please email any questions.
Hi all this is the first time we have used pixel harbor and understand the budget was too low for this project. We have now increased the budget to $2,000 and extended the deadline by another week
Hi all we are receiving some really great designs. I just added an example of the space that the web app will be going into... It is called "morvelapp.pdf"
Hi guys updated the brief. Hopefully this will help with the dashboard part of the design

```html
<!DOCTYPE html>
<html lang="en">
<head>
<meta charset="utf-8">
<title>VantiQor Dashboard – My Results</title>
<link rel="stylesheet" href="https://fonts.googleapis.com/css2?family=Open+Sans:wght@400;600&display=swap">
<style>
:root{
  --green:#7dc13a;
  --ink:#2b2b2b;
  --muted:#9a9a9a;
  --slate:#555b55;
  --bar-top:#ececec;
  --bar-bottom:#dcdcdc;
  --panel:#ebebeb;
  --white:#ffffff;
  --active:#1f6fbf;
  --link:#e8400c;
  --badge:#f04e1a;
  --icon:#4d524d;
  --rule:#ececec;
}
*{box-sizing:border-box;margin:0;padding:0}
html,body{width:1068px;height:1200px;overflow:hidden;background:var(--white);font-family:"Open Sans",sans-serif;color:var(--ink)}
.app{position:relative;width:1068px;height:1200px}

/* Header */
.site-header{position:absolute;left:0;top:0;width:1068px;height:144px;background:var(--white)}
.brand{position:absolute;left:26px;top:70px;display:flex;align-items:center;gap:12px}
.brand-mark{width:26px;height:26px;background:var(--green);border-radius:4px}
.brand-name{font-size:44px;font-weight:400;letter-spacing:1px;color:var(--ink);line-height:1}
.main-tabs{position:absolute;left:500px;top:41px;display:flex}
.main-tab{width:150px;height:103px;display:flex;flex-direction:column;align-items:center;justify-content:center;gap:8px;font-size:15px;color:var(--muted)}
.main-tab.is-active{width:177px;background:var(--panel);border-radius:12px 12px 0 0;color:var(--green)}
.main-tab svg{display:block}
.social{position:absolute;left:893px;top:90px;display:flex;gap:15px}
.social-dot{width:40px;height:40px;border-radius:50%;background:var(--green)}

/* Icon bar */
.dash-nav{position:absolute;left:0;top:144px;width:1068px;height:192px;background:linear-gradient(var(--bar-top),var(--bar-bottom))}
.dash-item{position:absolute;top:41px;width:130px;margin-left:-65px;text-align:center;font-size:16px;line-height:18px;color:var(--ink)}
.dash-item.is-active{color:var(--active)}
.dash-icon{position:relative;width:88px;height:88px;margin:0 auto 10px;border-radius:50%;background:radial-gradient(circle at 50% 35%,#ffffff 55%,#dcdcdc);box-shadow:0 3px 6px rgba(0,0,0,.25);display:flex;align-items:center;justify-content:center}
.dash-icon svg{display:block}
.person-fill{width:56px;height:56px;border-radius:50%;background:linear-gradient(#6a706a,#4d524d)}
.badge{position:absolute;right:-10px;top:-4px;width:40px;height:26px;border-radius:6px;background:var(--badge);color:var(--white);font-size:15px;line-height:26px;text-align:center}
.pointer{position:absolute;left:452px;bottom:0;width:0;height:0;border-left:12px solid transparent;border-right:12px solid transparent;border-bottom:12px solid var(--white)}

/* Results panel */
.results-wrap{position:absolute;left:24px;top:373px;width:1014px;height:329px;background:var(--panel);border-radius:14px}
.results-card{position:absolute;left:16px;top:23px;width:981px;height:283px;background:var(--white);border-radius:12px;overflow:hidden}
.results-title{height:67px;background:var(--green);color:var(--white);font-size:28px;font-weight:400;line-height:67px;padding-left:22px}
.results-table{width:100%;border-collapse:collapse}
.results-table th{height:52px;background:var(--slate);color:var(--white);font-size:19px;font-weight:400;text-align:left}
.results-table td{height:50px;font-size:17px;border-bottom:1px solid var(--rule)}
.results-table tr:last-child td{border-bottom:none}
.col-first{padding-left:21px;width:165px}
.col-last{width:141px}
.col-order{width:127px}
.col-date{width:323px}
.view-link{color:var(--link);text-decoration:none}
</style>
</head>
<body>
<div class="app">

  <header class="site-header">
    <div class="brand">
      <span class="brand-mark"></span>
      <span class="brand-name">VantiQor</span>
    </div>

    <nav class="main-tabs">
      <div class="main-tab">
        <svg width="48" height="34" viewBox="0 0 48 34"><rect x="6" y="2" width="36" height="24" rx="3" fill="#a8a8a8"/><rect x="0" y="27" width="48" height="5" rx="2" fill="#a8a8a8"/></svg>
        <span>ORDER A TEST</span>
      </div>
      <div class="main-tab is-active">
        <svg width="38" height="38" viewBox="0 0 38 38"><rect x="10" y="2" width="26" height="22" rx="2" fill="none" stroke="#7dc13a" stroke-width="3"/><rect x="2" y="12" width="26" height="22" rx="2" fill="#fff" stroke="#7dc13a" stroke-width="3"/><rect x="2" y="12" width="26" height="6" fill="#7dc13a"/></svg>
        <span>DASHBOARD</span>
      </div>
    </nav>

    <div class="social">
      <span class="social-dot"></span>
      <span class="social-dot"></span>
      <span class="social-dot"></span>
    </div>
  </header>

  <nav class="dash-nav">
    <div class="dash-item" style="left:66px">
      <div class="dash-icon">
        <svg width="50" height="50" viewBox="0 0 50 50"><rect x="4" y="6" width="42" height="30" rx="4" fill="none" stroke="#4d524d" stroke-width="4"/><polyline points="10,22 18,22 22,14 27,30 31,20 40,20" fill="none" stroke="#4d524d" stroke-width="3"/><rect x="20" y="36" width="10" height="6" fill="#4d524d"/><rect x="13" y="42" width="24" height="4" rx="2" fill="#4d524d"/></svg>
      </div>
      My<br>Confirmation
    </div>
    <div class="dash-item" style="left:199px">
      <div class="dash-icon">
        <svg width="50" height="50" viewBox="0 0 50 50"><rect x="22" y="4" width="10" height="24" rx="3" transform="rotate(-30 27 16)" fill="#4d524d"/><path d="M14 44 Q14 30 28 30" fill="none" stroke="#4d524d" stroke-width="4"/><rect x="8" y="42" width="34" height="5" rx="2" fill="#4d524d"/><rect x="24" y="32" width="16" height="4" fill="#4d524d"/></svg>
      </div>
      My<br>Nearest Lab
    </div>
    <div class="dash-item" style="left:330px">
      <div class="dash-icon">
        <svg width="40" height="54" viewBox="0 0 40 54"><path d="M10 2 C10 18 30 18 30 27 C30 36 10 36 10 52" fill="none" stroke="#4d524d" stroke-width="4"/><path d="M30 2 C30 18 10 18 10 27 C10 36 30 36 30 52" fill="none" stroke="#4d524d" stroke-width="4"/><line x1="12" y1="8" x2="28" y2="8" stroke="#4d524d" stroke-width="3"/><line x1="12" y1="46" x2="28" y2="46" stroke="#4d524d" stroke-width="3"/></svg>
      </div>
      My Orders
    </div>
    <div class="dash-item is-active" style="left:464px">
      <div class="dash-icon">
        <svg width="44" height="54" viewBox="0 0 44 54"><rect x="3" y="6" width="38" height="46" rx="4" fill="none" stroke="#1f6fbf" stroke-width="4"/><rect x="14" y="2" width="16" height="8" rx="2" fill="#1f6fbf"/><polyline points="9,32 16,32 19,24 24,40 28,28 35,28" fill="none" stroke="#1f6fbf" stroke-width="3"/></svg>
      </div>
      My Results
    </div>
    <div class="dash-item" style="left:595px">
      <div class="dash-icon">
        <svg width="44" height="54" viewBox="0 0 44 54"><rect x="3" y="6" width="38" height="46" rx="4" fill="none" stroke="#4d524d" stroke-width="4"/><rect x="14" y="2" width="16" height="8" rx="2" fill="#4d524d"/><g fill="#4d524d"><rect x="10" y="17" width="5" height="4"/><rect x="18" y="17" width="16" height="4"/><rect x="10" y="26" width="5" height="4"/><rect x="18" y="26" width="16" height="4"/><rect x="10" y="35" width="5" height="4"/><rect x="18" y="35" width="16" height="4"/></g></svg>
      </div>
      My Receipts
    </div>
    <div class="dash-item" style="left:726px">
      <div class="dash-icon">
        <div class="person-fill" role="img" aria-label="Account holder avatar"></div>
      </div>
      My Account
    </div>
    <div class="dash-item" style="left:863px">
      <div class="dash-icon">
        <svg width="52" height="38" viewBox="0 0 52 38"><rect x="2" y="2" width="48" height="34" rx="2" fill="#4d524d"/><polyline points="4,4 26,22 48,4" fill="none" stroke="#fff" stroke-width="2"/><line x1="4" y1="34" x2="20" y2="18" stroke="#fff" stroke-width="2"/><line x1="48" y1="34" x2="32" y2="18" stroke="#fff" stroke-width="2"/></svg>
        <span class="badge">2</span>
      </div>
      My Inbox
    </div>
    <div class="dash-item" style="left:995px">
      <div class="dash-icon">
        <div class="person-fill" role="img" aria-label="Customer service agent with headset"></div>
      </div>
      Contact Us
    </div>
    <span class="pointer"></span>
  </nav>

  <section class="results-wrap">
    <div class="results-card">
      <h1 class="results-title">MY RESULTS</h1>
      <table class="results-table">
        <thead>
          <tr><th class="col-first">First Name</th><th class="col-last">Last Name</th><th class="col-order">Order ID</th><th class="col-date">Date Created</th><th></th></tr>
        </thead>
        <tbody>
          <tr><td class="col-first">Dale</td><td>Morrow</td><td>32598</td><td>8/10/2013</td><td><a class="view-link" href="#">View Results</a></td></tr>
          <tr><td class="col-first">Dale</td><td>Morrow</td><td>32598</td><td>8/10/2013</td><td><a class="view-link" href="#">View Results</a></td></tr>
          <tr><td class="col-first">Dale</td><td>Morrow</td><td>32598</td><td>8/10/2013</td><td><a class="view-link" href="#">View Results</a></td></tr>
        </tbody>
      </table>
    </div>
  </section>

</div>
</body>
</html>
```